AMAZING WEBSITE DESIGN NEEDED FOR MAID / CLEANING SERVICE

NOTE: This is Website Design Only - No coding required

Please submit your designs ASAP as we want to pick a winner and get started!

Hey,

We are looking for a new amazing website design for a maid or cleaning service.

They have a horrible website that we want turned into a masterpiece.

As you will see on their current site:

http://brightnookservices.example-host.net/

They have a lot of stuff, very disorganized, and need help.

Here is what we need:

Colors: Same as current site, Orange, Gray, Black

Menu: Horizontal with same Menu items

Need a spot for a video on the homepage

Want content to be structured in a great format that is easy to read.

Want to highlight commercial and residential on the website homepage.

Also want a spot for customer testimonials

We want the site clean, professional, fresh and modern.

Please help by matching the logo design.

I look forward to your designs!
Updates

Hi All! Really appreciate your efforts and designs. I will be meeting with our client on Monday and will then be able to provide feedback after our meeting. If you have other ideas, please submit them. The more I can show him the better! Thanks!

Target Market(s)

The target market is residential home owners as well as commercial businesses who need cleaning on a regular basis.

This company cleans homes and offices for individuals.

Industry/Entity Type

Residential

Font styles to use
Sans Serif

Requirements
Must have
• Must match logo colors
Must have spot for video
Must have a clean look
Must have a bold look
Nice to have
• Highly visual
Should not have
• clutter
messy design
hard to read

```html
<!DOCTYPE html>
<html lang="en">
<head>
<meta charset="utf-8">
<title>Bright Nook – Quality Commercial &amp; Residential Cleaning</title>
<link rel="stylesheet" href="https://fonts.googleapis.com/css2?family=Mulish:ital,wght@0,400;0,600;0,700;0,800;1,400&family=Open+Sans:ital,wght@0,400;0,600;0,700;1,400&display=swap">
<style>
  :root{
    --orange:#f47a1f;
    --orange-light:#f99a3c;
    --ink:#1d1d1d;
    --text:#3a3a3a;
    --muted:#777;
    --band:#f2f2f2;
    --rule:#e4e4e4;
    --footer-top:#2b2b2b;
    --footer-bottom:#1c1c1c;
    --white:#fff;
  }
  *{box-sizing:border-box;margin:0;padding:0}
  html,body{width:721px;height:1200px;overflow:hidden;background:var(--white)}
  body{font-family:"Open Sans",Arial,sans-serif;color:var(--text)}
  .page{position:relative;width:721px;height:1200px;overflow:hidden}
  .abs{position:absolute}

  /* header */
  .brand{left:65px;top:30px;display:flex;align-items:center;gap:8px}
  .brand-mark{width:22px;height:22px;background:var(--orange)}
  .brand-name{font-family:"Mulish",sans-serif;font-weight:800;font-size:22px;color:var(--ink);letter-spacing:-.3px}
  .brand-tag{left:95px;top:66px;font-family:"Mulish",sans-serif;font-size:7.5px;font-weight:700;color:#555}
  .hire{right:66px;top:41px;text-align:right;font-family:"Mulish",sans-serif}
  .hire-label{font-size:12px;color:var(--orange)}
  .hire-phone{font-size:16.5px;color:#333;margin-top:1px}

  /* nav */
  .nav{left:0;top:85px;width:721px;height:30px;background:linear-gradient(var(--orange-light),var(--orange));display:flex;justify-content:center}
  .nav a{font-family:"Mulish",sans-serif;color:var(--white);font-size:10.5px;text-decoration:none;line-height:30px;padding:0 9.5px;border-right:1px solid rgba(0,0,0,.15)}
  .nav a:last-child{border-right:0}

  /* hero */
  .hero{left:0;top:115px;width:721px;height:278px;background:linear-gradient(180deg,#e9e6e1 0%,#d8d2c8 45%,#8a5a3b 85%,#6b4128 100%)}
  .hero-title{left:62px;top:224px;font-family:"Mulish",sans-serif;font-weight:800;font-size:26px;color:var(--ink)}
  .hero-sub{left:62px;top:259px;font-family:"Mulish",sans-serif;font-size:20px;color:var(--ink)}
  .dots{left:318px;top:377px;display:flex;gap:3px}
  .dots i{width:6px;height:6px;border-radius:50%;background:rgba(255,255,255,.6)}
  .dots i:first-child{background:var(--white)}

  /* welcome */
  .welcome{left:0;top:422px;width:721px;text-align:center}
  .welcome h1{font-family:"Mulish",sans-serif;font-weight:400;font-size:22px;color:var(--ink)}
  .welcome .lead{width:580px;margin:8px auto 0;font-size:9.4px;line-height:12px;color:#333}
  .welcome .body{width:580px;margin:7px auto 0;font-size:8px;line-height:12px;color:var(--muted)}
  .btns{left:275px;top:536px;display:flex;gap:6px}
  .btn{width:85px;height:25px;border-radius:2px;color:var(--white);font-family:"Mulish",sans-serif;font-size:8.5px;font-weight:700;display:flex;align-items:center;justify-content:center}
  .btn-orange{background:var(--orange)}
  .btn-dark{background:var(--ink)}

  /* services */
  .services{left:0;top:585px;width:721px;height:227px;background:var(--band);border-top:1px solid var(--rule);border-bottom:1px solid var(--rule)}
  .card{top:620px;width:180px}
  .card-photo{width:180px;height:86px;border:3px solid var(--white);box-shadow:0 0 2px rgba(0,0,0,.15)}
  .card h2{font-family:"Mulish",sans-serif;font-weight:400;font-size:15.5px;color:var(--orange);margin-top:10px}
  .card p{font-size:7.2px;line-height:12px;color:#666;margin-top:3px;padding-left:1px}
  .card .more{font-size:7.5px;font-weight:700;color:var(--ink);margin-top:4px;padding-left:1px}
  .video{left:456px;top:617px;width:206px;height:148px;border:4px solid var(--white);box-shadow:0 0 3px rgba(0,0,0,.18);background:linear-gradient(135deg,#cfe7b0,#f3e15a 45%,#4fb4c6)}
  .play{left:544px;top:676px}

  /* testimonials */
  .testi-title{left:0;top:840px;width:721px;text-align:center;font-family:"Mulish",sans-serif;font-size:18px;color:var(--ink)}
  .quote{top:880px;width:205px}
  .avatar{width:52px;height:52px;border-radius:50%;border:3px solid var(--white);box-shadow:0 0 3px rgba(0,0,0,.25)}
  .quote p{font-style:italic;font-size:7.9px;line-height:12.5px;color:#777}
  .quote .by{font-family:"Mulish",sans-serif;font-size:9px;color:var(--ink);margin-top:5px}
  .quote .city{font-size:7px;color:#777;margin-top:4px}

  /* footer */
  .footer{left:0;top:1010px;width:721px;height:150px;background:linear-gradient(var(--footer-top),var(--footer-bottom))}
  .fcol{top:1038px}
  .fcol h3{font-family:"Mulish",sans-serif;font-weight:400;font-size:12px;color:var(--white);margin-bottom:6px}
  .fcol li{list-style:none;font-size:7.5px;line-height:14px;color:#e8e8e8;padding-left:1px}
  .social{display:flex;gap:3px;margin-top:2px}
  .social i{width:18px;height:18px;border-radius:50%;background:var(--white)}
  .bottom{left:0;top:1160px;width:721px;height:40px;background:var(--footer-bottom);border-top:1px solid #333}
  .copy{left:62px;top:1175px;font-size:7px;color:#888}
</style>
</head>
<body>
<div class="page">

  <header>
    <div class="abs brand"><span class="brand-mark"></span><span class="brand-name">Bright Nook</span></div>
    <div class="abs brand-tag">Quality Commercial &amp; Residential Cleaning</div>
    <div class="abs hire">
      <div class="hire-label">Hire Us Now</div>
      <div class="hire-phone">(505) 555-0142</div>
    </div>
  </header>

  <nav class="abs nav">
    <a href="#">Home</a><a href="#">About Us</a><a href="#">Services</a><a href="#">Our Employees</a><a href="#">Why Choose Us?</a><a href="#">Testimonials</a><a href="#">Speical Offers</a><a href="#">Contact Us</a>
  </nav>

  <section>
    <div class="abs hero" role="img" aria-label="Bright open-plan living room and kitchen with wooden floors and a staircase"></div>
    <div class="abs hero-title">Mauris vel lacus vitae</div>
    <div class="abs hero-sub">Suspendisse vulputate aliquamdu</div>
    <div class="abs dots"><i></i><i></i><i></i><i></i></div>
  </section>

  <section class="abs welcome">
    <h1>Welcome to Our Website Mainpage</h1>
    <p class="lead">Thank you for visiting us! You are one step closer to experiencing first class maid service! Our company specializes in detailed housekeeping, janitorial, and commerical cleaning services making your environment shine and sparkle like it never has before!</p>
    <p class="body">Our maids are fully trained professionals who we recruit from high end luxury hotels we know, like the Grandview and Harborline! We pride ourselves in delivering exceptional service to our valued customers by fully understanding what your expectations &amp; needs are! We will strive for perfection and we will provide an uncompromising commitment to excellence!</p>
  </section>
  <div class="abs btns"><span class="btn btn-orange">READ MORE</span><span class="btn btn-dark">SPECIAL OFFER</span></div>

  <section>
    <div class="abs services"></div>
    <article class="abs card" style="left:61px">
      <div class="card-photo" role="img" aria-label="Office desk with a lamp and plant by a window" style="background:linear-gradient(#d9d3c6,#8c8170)"></div>
      <h2>Commercial Service</h2>
      <p>Malesuada nec ultricies sit amet porttitor mattis enim In massa libero interdum nec interdum</p>
      <div class="more">View More ›</div>
    </article>
    <article class="abs card" style="left:258px">
      <div class="card-photo" role="img" aria-label="Cosy living room with a sofa and rug" style="background:linear-gradient(#efe8dc,#b9906a)"></div>
      <h2>Residential Service</h2>
      <p>Malesuada nec ultricies sit amet porttitor mattis enim In massa libero interdum nec interdum</p>
      <div class="more">View More ›</div>
    </article>
    <div class="abs video" role="img" aria-label="Video: person in yellow gloves holding cleaning supplies"></div>
    <svg class="abs play" width="28" height="28" viewBox="0 0 28 28"><circle cx="14" cy="14" r="13" fill="#222" stroke="#fff" stroke-width="1.5"/><path d="M11 8.5 L19.5 14 L11 19.5Z" fill="#fff"/></svg>
  </section>

  <section>
    <h2 class="abs testi-title">Customer Testimonials</h2>
    <div class="abs avatar" style="left:80px;top:877px;background:#d8c8b8" role="img" aria-label="Customer portrait"></div>
    <div class="abs quote" style="left:139px">
      <p>Pellentesque faucibus Ut accumsan ultricies elit Maecenas at justo id velit placerat molestie Donec dictum lectus non odio Cras a ante vitae enim iaculis aliquam Mauris nunc quam venenatis nec euismod sit amet egestas placerat est Pellentesque habitant</p>
      <div class="by">By Author Name</div>
      <div class="city">Location/City</div>
    </div>
    <div class="abs avatar" style="left:390px;top:877px;background:#6a4a38" role="img" aria-label="Customer portrait"></div>
    <div class="abs quote" style="left:449px">
      <p>Maecenas at justo id velit placerat molestie Donec dictum lectus non odio Cras a ante vitae enim iaculis aliquam Mauris nunc quam venenatis nec euismod sit amet egestas placerat est Pellentesque habitant morbi tristique</p>
      <div class="by">By Author Name</div>
      <div class="city">Location/City</div>
    </div>
  </section>

  <footer>
    <div class="abs footer"></div>
    <div class="abs fcol" style="left:63px"><h3>Company</h3><ul><li>Home</li><li>Our Services</li><li>Our Employees</li><li>Why Choose Bright Nook?</li><li>What Our Customers Are Saying</li></ul></div>
    <div class="abs fcol" style="left:207px"><h3>Resources</h3><ul><li>Special Offers</li><li>About Us</li><li>Contact Us</li><li>Request a Bid</li><li>Meet the President &amp; CEO</li></ul></div>
    <div class="abs fcol" style="left:344px"><h3>Contact Us</h3><ul><li>4120 Mesa Verde Lane Suite 310</li><li>Riverton | New Mexico | 87000</li><li>(505) 555-0142 Office</li><li>(505) 555-0178 Fax</li><li>hello@brightnook.example</li></ul></div>
    <div class="abs fcol" style="left:513px"><h3>Get Connected</h3><div class="social"><i></i><i></i><i></i><i></i></div></div>
    <div class="abs bottom"></div>
    <div class="abs copy">© 2014 Company Name  All right reserved  Term of Use</div>
  </footer>

</div>
</body>
</html>
```